Business Card Design

We need a business card designed for our new company. Prefer a black card with white logo & writing.

Contact Information for Business Card

Ted Galloway, address: 7-4812 Fernhollow Road, Abbotsford, BC, V3K 8R2, Office Phone: 604-712-3390, Cell: 604-947-2164, Email: ted@resinworkshub.ca

Colors

Designer to choose only greyscale colors for use in the design.

```html
<!DOCTYPE html>
<html lang="en">
<head>
<meta charset="utf-8">
<title>Resin Works Hub – Business Card</title>
<link href="https://fonts.googleapis.com/css2?family=Montserrat:wght@400;700;800&display=swap" rel="stylesheet">
<style>
  :root {
    --page: #d9d9d9;
    --card: #262626;
    --ink: #ffffff;
    --ink-soft: #d6d6d6;
    --emboss: #121212;
  }
  * { box-sizing: border-box; margin: 0; padding: 0; }
  html, body { width: 900px; height: 1200px; overflow: hidden; }
  body {
    background: var(--page);
    font-family: "Montserrat", Arial, sans-serif;
    position: relative;
  }
  .card {
    position: absolute;
    left: 80px;
    width: 742px;
    height: 442px;
    background: var(--card);
    border-radius: 24px;
  }
  .card--front { top: 130px; }
  .card--back { top: 638px; }

  .brand {
    position: absolute;
    left: 80px; width: 270px;
    top: 0; height: 100%;
    display: flex; flex-direction: column;
    align-items: center; justify-content: center;
    color: var(--ink);
    font-weight: 800;
    text-transform: uppercase;
    line-height: 1.05;
    white-space: nowrap;
  }
  .brand__main { font-size: 33px; letter-spacing: 0.3px; }
  .brand__sub { font-size: 19px; letter-spacing: 9px; margin-top: 10px; padding-left: 9px; }

  .divider {
    position: absolute;
    left: 371px; top: 128px;
    width: 2px; height: 224px;
    background: var(--ink);
  }
  .details {
    position: absolute;
    left: 392px; top: 124px;
    color: var(--ink-soft);
  }
  .details__name { color: var(--ink); font-size: 25px; font-weight: 700; line-height: 1; }
  .details__role { font-size: 15px; margin-top: 11px; }
  .details__address { font-size: 16px; line-height: 20px; margin-top: 13px; }
  .contact { list-style: none; margin-top: 13px; }
  .contact li {
    display: flex; align-items: center;
    font-size: 16px; height: 26px;
  }
  .contact li + li { margin-top: 2px; }
  .contact svg { width: 16px; height: 16px; margin-right: 14px; fill: var(--ink); flex: none; }

  .brand--back { left: 0; width: 100%; color: var(--emboss); }
  .brand--back .brand__main { font-size: 52px; }
  .brand--back .brand__sub { font-size: 28px; letter-spacing: 13px; padding-left: 13px; }
</style>
</head>
<body>
  <section class="card card--front">
    <div class="brand">
      <span class="brand__main">Resin Works</span>
      <span class="brand__sub">Hub</span>
    </div>
    <div class="divider"></div>
    <div class="details">
      <p class="details__name">Ted Galloway</p>
      <p class="details__role">owner</p>
      <p class="details__address">7-4812 Fernhollow Road,<br>Abbotsford, BC, V3K 8R2</p>
      <ul class="contact">
        <li><svg viewBox="0 0 24 24" aria-hidden="true"><path d="M6.6 10.8c1.4 2.8 3.8 5.1 6.6 6.6l2.2-2.2c.3-.3.7-.4 1-.2 1.1.4 2.3.6 3.6.6.6 0 1 .4 1 1V20c0 .6-.4 1-1 1C10.6 21 3 13.4 3 4c0-.6.4-1 1-1h3.5c.6 0 1 .4 1 1 0 1.3.2 2.5.6 3.6.1.3 0 .7-.2 1z"/></svg>604-712-3390</li>
        <li><svg viewBox="0 0 24 24" aria-hidden="true"><path d="M7 1h10a2 2 0 0 1 2 2v18a2 2 0 0 1-2 2H7a2 2 0 0 1-2-2V3a2 2 0 0 1 2-2zm0 3v14h10V4zm5 15.5a1.2 1.2 0 1 0 0 2.4 1.2 1.2 0 0 0 0-2.4z"/></svg>604-947-2164</li>
        <li><svg viewBox="0 0 24 24" aria-hidden="true"><path d="M2 5h20v14H2zm2 2v.5l8 5 8-5V7z"/></svg>ted@resinworkshub.ca</li>
        <li><svg viewBox="0 0 24 24" aria-hidden="true"><path d="M12 2a10 10 0 1 0 0 20 10 10 0 0 0 0-20zm-1 17.9A8 8 0 0 1 4.2 10l4.8 4.8v1a2 2 0 0 0 2 2zm6.9-2.5A2 2 0 0 0 16 16h-1v-3a1 1 0 0 0-1-1H8v-2h2a1 1 0 0 0 1-1V7h2a2 2 0 0 0 2-2v-.4a8 8 0 0 1 2.9 12.8z"/></svg>www.resinworkshub.ca</li>
      </ul>
    </div>
  </section>

  <section class="card card--back">
    <div class="brand brand--back">
      <span class="brand__main">Resin Works</span>
      <span class="brand__sub">Hub</span>
    </div>
  </section>
</body>
</html>
```